Präsentationsvorlagen für Vorträge
Zielgruppe
Wir machen laborbasierte Selbsttests im Bereich Longevity und bieten dazu auch passende Supplements an
Aufgabenstellung
Ich brauche eine Präsentationsvorlage für Vorträge basierend auf den Farben und Logo in den angehängten Dateien. Soll alles was für Präsentation nötig ist berücksichtigen

```html
<!DOCTYPE html>
<html lang="de">
<head>
<meta charset="utf-8">
<title>Kernvital – Präsentationsvorlage</title>
<link href="https://fonts.googleapis.com/css2?family=Montserrat:wght@400;500;600;700;800&display=swap" rel="stylesheet">
<style>
:root{
  --teal:#0b5550;
  --teal-dark:#083f3c;
  --green:#8cc63f;
  --green-soft:#c9e4a2;
  --ink:#1d3a3a;
  --muted:#6b7b7a;
  --line:#d9dedd;
  --stage:#e4e5e6;
  --page:#f2f3f3;
}
*{margin:0;padding:0;box-sizing:border-box}
html,body{width:1200px;height:2475px;overflow:hidden}
body{background:linear-gradient(var(--stage) 0 830px,var(--page) 830px);font-family:'Montserrat',sans-serif;color:var(--ink);position:relative}
.slide{position:absolute;width:343px;height:193px;background:#fff;overflow:hidden;box-shadow:0 1px 4px rgba(0,0,0,.08)}
.slide.hero{transform:scale(1.25);transform-origin:0 0;box-shadow:0 8px 24px rgba(0,0,0,.18)}
.dark{background:var(--teal);color:#fff}
.brand{position:absolute;top:10px;right:13px;display:flex;align-items:center;gap:3px;font-weight:700;font-size:8px;color:var(--teal)}
.brand i{width:6px;height:6px;border-radius:50%;background:var(--green)}
.dark .brand,.on-photo .brand{color:#fff}
.title{position:absolute;left:32px;top:30px;font-weight:700;font-size:11px;line-height:1.25;color:var(--ink)}
.dark .title{color:#fff}
.hl{background:var(--green);color:#fff;border-radius:6px;padding:0 3px}
.p{font-size:4px;line-height:1.55;color:var(--muted)}
.dark .p{color:#d5e6e4}
.b{font-weight:700;color:var(--ink);font-size:4.5px}
.g{color:var(--green);font-weight:700}
.abs{position:absolute}
.foot{position:absolute;left:12px;bottom:7px;font-size:3px;color:#b5bcbb}
.num{position:absolute;right:12px;bottom:6px;width:7px;height:7px;border:1px solid var(--line);border-radius:50%;font-size:3.5px;text-align:center;line-height:5px;color:var(--muted)}
.photo{position:absolute;background:linear-gradient(135deg,#b9c9b2,#6f8a72 60%,#49604f)}
.photo.room{background:linear-gradient(135deg,#efe9e2,#c7b8a6 60%,#8f7f6f)}
.photo.blue{background:linear-gradient(135deg,#d8e6ef,#8db3c8 55%,#5a7e93)}
.photo.grey{background:linear-gradient(135deg,#9da7a4,#59645f 60%,#2f3936)}
.frame{border-right:3px solid var(--green);border-bottom:3px solid var(--green);border-radius:0 0 8px 0}
.card{position:absolute;background:#fff;border-radius:4px;box-shadow:0 1px 5px rgba(0,0,0,.1)}
.tick{position:absolute;width:10px;height:10px;border-radius:50%;background:var(--green)}
.tick::after{content:"";position:absolute;left:3px;top:2px;width:3px;height:5px;border:solid #fff;border-width:0 1.2px 1.2px 0;transform:rotate(45deg)}
.cover-title{position:absolute;left:25px;top:75px;font-size:18px;line-height:1.05;font-weight:500}
.cover-title strong{display:block;color:var(--green);font-weight:700}
.cover-sub{font-size:8px;margin-top:3px}
.pill{position:absolute;left:22px;bottom:14px;font-size:5px;padding:2px 6px;border:1px solid currentColor;border-radius:8px}
.toc{position:absolute;left:185px;top:50px;width:128px}
.toc div{display:flex;justify-content:space-between;align-items:flex-end;border-bottom:1px solid var(--line);height:23px;font-size:5px;font-weight:600;padding-bottom:3px}
.toc span{color:var(--green);font-size:10px;font-weight:400}
.bar-row{height:3px;background:#e5e9e8;border-radius:2px;margin:3px 0 8px}
.bar-row i{display:block;height:3px;background:var(--green);border-radius:2px}
table{border-collapse:collapse;width:100%;font-size:3.5px}
td,th{padding:2.5px 4px;text-align:left}
</style>
</head>
<body>

<!-- Staged feature area, drawn flat -->
<section class="slide hero" style="left:275px;top:100px;z-index:1">
  <div class="brand"><i></i>Kernvital</div>
  <div class="title" style="top:28px">About <span class="hl">us</span></div>
  <div class="abs g" style="left:32px;top:47px;font-size:4.5px">Welcome to Kernvital</div>
  <div class="abs p" style="left:32px;top:55px;width:125px">Lorem ipsum dolor sit amet, consectetuer adipiscing elit, sed diam nonummy nibh euismod tincidunt ut laoreet dolore magna aliquam erat volutpat. Ut wisi enim ad minim veniam, quis nostrud exerci tation ullamcorper suscipit lobortis nisl ut aliquip ex ea commodo consequat.</div>
  <div class="abs p" style="left:32px;top:110px;width:120px;border-left:1.5px solid var(--green);padding-left:5px;font-style:italic">Lorem ipsum dolor sit amet, consectetuer adipiscing elit, sed diam nonummy nibh euismod tincidunt.</div>
  <div class="photo blue" style="left:200px;top:30px;width:100px;height:163px" role="img" aria-label="Portrait of a smiling doctor in a white coat"></div>
  <div class="abs" style="left:230px;top:150px;background:var(--green);color:#fff;font-size:4.5px;font-weight:700;padding:3px 6px">Dr. Jonas Beispiel</div>
  <div class="foot">Your presentation title goes here</div><div class="num">3</div>
</section>

<section class="slide hero" style="left:185px;top:360px;z-index:2">
  <div class="brand"><i></i>Kernvital</div>
  <div class="title" style="top:38px">Table <span class="hl">of</span><br>Content</div>
  <div class="abs p" style="left:32px;top:128px;width:125px;color:var(--teal)">Lorem ipsum dolor sit amet, consectetuer adipiscing elit, sed diam nonummy nibh euismod tincidunt ut laoreet dolore magna aliquam erat volutpat.</div>
  <div class="toc"><div>Introduction<span>03</span></div><div>Improving our Health<span>05</span></div><div>Why you should choose us<span>06</span></div><div>Our Product<span>07</span></div><div>Market Research<span>08</span></div></div>
  <div class="foot">Your presentation title goes here</div><div class="num">2</div>
</section>

<section class="slide hero" style="left:625px;top:455px;z-index:2">
  <div class="abs dark" style="left:0;top:0;width:210px;height:193px"></div>
  <div class="brand"><i></i>Kernvital</div>
  <div class="title" style="color:#fff;top:28px">Lorem <span class="hl">ipsum</span><br>dolor sit amet</div>
  <div class="abs p" style="left:32px;top:95px;width:120px;color:#d5e6e4">Lorem ipsum dolor sit amet, consectetuer adipiscing elit, sed diam nonummy nibh euismod tincidunt ut laoreet dolore magna aliquam erat volutpat. Ut wisi enim ad minim veniam, quis nostrud exerci tation ullamcorper suscipit lobortis nisl ut aliquip ex ea commodo consequat.</div>
  <div class="photo room frame" style="left:165px;top:58px;width:165px;height:100px" role="img" aria-label="Doctor showing a clipboard to an elderly woman"></div>
  <div class="num">4</div>
</section>

<section class="slide hero dark" style="left:605px;top:215px;z-index:3">
  <div class="photo" style="inset:0;background:linear-gradient(90deg,var(--teal) 30%,rgba(11,85,80,.55) 60%,#7a9a7a)" role="img" aria-label="Elderly couple jogging in a park"></div>
  <div class="brand" style="left:25px;right:auto;top:18px;font-size:11px"><i></i>Kernvital</div>
  <div class="cover-title">COMPANY<strong>PRESENTATION</strong><div class="cover-sub">Your subtitle texts goes here</div></div>
  <div class="pill">www.kernvital.de</div>
</section>

<!-- Row 1 -->
<section class="slide dark" style="left:95px;top:780px">
  <div class="photo" style="inset:0;background:linear-gradient(90deg,var(--teal) 30%,rgba(11,85,80,.55) 60%,#7a9a7a)" role="img" aria-label="Elderly couple jogging in a park"></div>
  <div class="brand" style="left:25px;right:auto;top:18px;font-size:11px"><i></i>Kernvital</div>
  <div class="cover-title">COMPANY<strong>PRESENTATION</strong><div class="cover-sub">Your subtitle texts goes here</div></div>
  <div class="pill">www.kernvital.de</div>
</section>

<section class="slide" style="left:453px;top:780px">
  <div class="photo" style="inset:0;background:linear-gradient(90deg,#fff 30%,rgba(255,255,255,.6) 55%,#9bb29a)" role="img" aria-label="Elderly couple jogging in a park"></div>
  <div class="brand" style="left:25px;right:auto;top:18px;font-size:11px"><i></i>Kernvital</div>
  <div class="cover-title" style="color:var(--teal)">COMPANY<strong>PRESENTATION</strong><div class="cover-sub">Your subtitle texts goes here</div></div>
  <div class="pill" style="color:var(--teal)">www.kernvital.de</div>
</section>

<section class="slide" style="left:811px;top:780px">
  <div class="brand"><i></i>Kernvital</div>
  <div class="title" style="top:38px">Table <span class="hl">of</span><br>Content</div>
  <div class="abs p" style="left:32px;top:128px;width:125px;color:var(--teal)">Lorem ipsum dolor sit amet, consectetuer adipiscing elit, sed diam nonummy nibh euismod tincidunt ut laoreet dolore magna aliquam erat volutpat.</div>
  <div class="toc"><div>Introduction<span>03</span></div><div>Improving our Health<span>05</span></div><div>Why you should choose us<span>06</span></div><div>Our Product<span>07</span></div><div>Market Research<span>08</span></div></div>
  <div class="foot">Your presentation title goes here</div><div class="num">2</div>
</section>

<!-- Row 2 -->
<section class="slide" style="left:95px;top:989px">
  <div class="brand"><i></i>Kernvital</div>
  <div class="title" style="top:28px">About <span class="hl">us</span></div>
  <div class="abs g" style="left:32px;top:47px;font-size:4.5px">Welcome to Kernvital</div>
  <div class="abs p" style="left:32px;top:55px;width:125px">Lorem ipsum dolor sit amet, consectetuer adipiscing elit, sed diam nonummy nibh euismod tincidunt ut laoreet dolore magna aliquam erat volutpat. Ut wisi enim ad minim veniam, quis nostrud exerci tation ullamcorper suscipit lobortis nisl ut aliquip ex ea commodo consequat.</div>
  <div class="abs p" style="left:32px;top:110px;width:120px;border-left:1.5px solid var(--green);padding-left:5px;font-style:italic">Lorem ipsum dolor sit amet, consectetuer adipiscing elit, sed diam nonummy nibh euismod tincidunt.</div>
  <div class="photo blue" style="left:200px;top:30px;width:100px;height:163px" role="img" aria-label="Portrait of a smiling doctor in a white coat"></div>
  <div class="abs" style="left:230px;top:150px;background:var(--green);color:#fff;font-size:4.5px;font-weight:700;padding:3px 6px">Dr. Jonas Beispiel</div>
  <div class="foot">Your presentation title goes here</div><div class="num">3</div>
</section>

<section class="slide" style="left:453px;top:989px">
  <div class="brand"><i></i>Kernvital</div>
  <div class="title">Six <span class="hl">Point</span> Slide</div>
  <div class="card" style="left:35px;top:60px;width:85px;height:45px"></div><div class="card" style="left:135px;top:60px;width:85px;height:45px"></div><div class="card" style="left:235px;top:60px;width:85px;height:45px"></div>
  <div class="card" style="left:35px;top:113px;width:85px;height:45px"></div><div class="card" style="left:135px;top:113px;width:85px;height:45px"></div><div class="card" style="left:235px;top:113px;width:85px;height:45px"></div>
  <div class="tick" style="left:28px;top:55px"></div><div class="tick" style="left:128px;top:55px"></div><div class="tick" style="left:228px;top:55px"></div>
  <div class="tick" style="left:28px;top:108px"></div><div class="tick" style="left:128px;top:108px"></div><div class="tick" style="left:228px;top:108px"></div>
  <div class="abs p" style="left:43px;top:65px;width:72px"><span class="b">Lorem ipsum dolor sit amet, consectetuer adipiscing</span><br>Lorem ipsum dolor sit amet, sed diam nonummy nibh.</div>
  <div class="abs p" style="left:143px;top:65px;width:72px"><span class="b">Lorem ipsum dolor sit amet, consectetuer adipiscing</span><br>Lorem ipsum dolor sit amet, sed diam nonummy nibh.</div>
  <div class="abs p" style="left:243px;top:65px;width:72px"><span class="b">Lorem ipsum dolor sit amet, consectetuer adipiscing</span><br>Lorem ipsum dolor sit amet, sed diam nonummy nibh.</div>
  <div class="abs p" style="left:43px;top:118px;width:72px"><span class="b">Lorem ipsum dolor sit amet, consectetuer adipiscing</span><br>Lorem ipsum dolor sit amet, sed diam nonummy nibh.</div>
  <div class="abs p" style="left:143px;top:118px;width:72px"><span class="b">Lorem ipsum dolor sit amet, consectetuer adipiscing</span><br>Lorem ipsum dolor sit amet, sed diam nonummy nibh.</div>
  <div class="abs p" style="left:243px;top:118px;width:72px"><span class="b">Lorem ipsum dolor sit amet, consectetuer adipiscing</span><br>Lorem ipsum dolor sit amet, sed diam nonummy nibh.</div>
  <div class="foot">Your presentation title goes here</div><div class="num">3</div>
</section>

<section class="slide" style="left:811px;top:989px">
  <div class="brand"><i></i>Kernvital</div>
  <div class="title" style="top:25px">Text slide <span class="hl">with</span><br>two column</div>
  <div class="abs p" style="left:32px;top:64px;width:120px"><span class="b">Our Vision</span><br><br>Lorem ipsum dolor sit amet, consectetuer adipiscing elit, sed diam nonummy nibh euismod tincidunt ut laoreet dolore magna aliquam erat volutpat. Ut wisi enim ad minim veniam, quis nostrud exerci tation ullamcorper suscipit lobortis nisl ut aliquip ex ea commodo consequat.</div>
  <div class="abs p" style="left:183px;top:64px;width:125px"><span class="b">Our Mission</span><br><br>• Lorem ipsum dolor sit amet, consectetuer adipiscing elit, sed diam nonummy.<br><br>• Lorem ipsum dolor sit amet, consectetuer adipiscing elit, sed diam nonummy.<br><br>• Lorem ipsum dolor sit amet, consectetuer adipiscing elit, sed diam nonummy.</div>
  <div class="foot">Your presentation title goes here</div><div class="num">4</div>
</section>

<!-- Row 3 -->
<section class="slide" style="left:95px;top:1198px">
  <div class="brand"><i></i>Kernvital</div>
  <div class="title" style="top:25px">Text slide <span class="hl">with</span><br>three column</div>
  <div class="abs p" style="left:32px;top:64px;width:90px"><span class="b">Lorem Ipsum</span><br><br>Lorem ipsum dolor sit amet, consectetuer adipiscing elit, sed diam nonummy nibh euismod tincidunt ut laoreet dolore magna aliquam erat volutpat. Ut wisi enim ad minim veniam, quis nostrud exerci tation.</div>
  <div class="abs p" style="left:133px;top:78px;width:90px">Lorem ipsum dolor sit amet, consectetuer adipiscing elit, sed diam nonummy nibh euismod tincidunt ut laoreet dolore magna aliquam erat volutpat. Ut wisi enim ad minim veniam, quis nostrud exerci tation.</div>
  <div class="abs p" style="left:234px;top:78px;width:90px">Lorem ipsum dolor sit amet, consectetuer adipiscing elit, sed diam nonummy nibh euismod tincidunt ut laoreet dolore magna aliquam erat volutpat. Ut wisi enim ad minim veniam, quis nostrud exerci tation.</div>
  <div class="foot">Your presentation title goes here</div><div class="num">4</div>
</section>

<section class="slide" style="left:453px;top:1198px">
  <div class="brand"><i></i>Kernvital</div>
  <div class="title" style="left:26px;top:40px">What <span class="hl">we</span> do?</div>
  <div class="abs p" style="left:26px;top:58px;width:160px">Lorem ipsum dolor sit amet, consectetuer adipiscing elit, sed diam nonummy nibh euismod tincidunt ut laoreet dolore magna aliquam erat volutpat.</div>
  <div class="tick" style="left:26px;top:95px;background:none;border:1px solid var(--green)"></div><div class="tick" style="left:115px;top:95px;background:none;border:1px solid var(--green)"></div>
  <div class="tick" style="left:26px;top:125px;background:none;border:1px solid var(--green)"></div><div class="tick" style="left:115px;top:125px;background:none;border:1px solid var(--green)"></div>
  <div class="abs p" style="left:42px;top:95px;width:65px;color:var(--teal)">Lorem ipsum dolor sit amet, consectetuer adipiscing elit.</div>
  <div class="abs p" style="left:131px;top:95px;width:65px;color:var(--teal)">Lorem ipsum dolor sit amet, consectetuer adipiscing elit.</div>
  <div class="abs p" style="left:42px;top:125px;width:65px;color:var(--teal)">Lorem ipsum dolor sit amet, consectetuer adipiscing elit.</div>
  <div class="abs p" style="left:131px;top:125px;width:65px;color:var(--teal)">Lorem ipsum dolor sit amet, consectetuer adipiscing elit.</div>
  <div class="photo blue frame" style="left:218px;top:35px;width:110px;height:125px;border-top:3px solid var(--green);border-radius:0 8px 8px 0" role="img" aria-label="Happy elderly couple embracing"></div>
  <div class="foot">Your presentation title goes here</div><div class="num">5</div>
</section>

<section class="slide" style="left:811px;top:1198px">
  <div class="brand"><i></i>Kernvital</div>
  <div class="title" style="top:42px"><span class="hl">Our</span> Value</div>
  <div class="abs p" style="left:135px;top:42px;width:175px">Lorem ipsum dolor sit amet, consectetuer adipiscing elit, sed diam nonummy nibh euismod tincidunt ut laoreet dolore magna aliquam erat volutpat.</div>
  <div class="abs p" style="left:35px;top:80px;width:120px"><span style="color:var(--green);font-size:10px">01</span> <span class="b">Lorem Ipsum</span> Lorem ipsum dolor sit amet.</div>
  <div class="abs p" style="left:48px;top:108px;width:120px"><span style="color:var(--green);font-size:10px">02</span> <span class="b">Lorem Ipsum</span> Lorem ipsum dolor sit amet.</div>
  <div class="abs p" style="left:35px;top:136px;width:120px"><span style="color:var(--green);font-size:10px">03</span> <span class="b">Lorem Ipsum</span> Lorem ipsum dolor sit amet.</div>
  <div class="abs p" style="left:170px;top:80px;width:130px"><span style="color:var(--green);font-size:10px">04</span> <span class="b">Lorem Ipsum</span> Lorem ipsum dolor sit amet.</div>
  <div class="abs p" style="left:183px;top:108px;width:130px"><span style="color:var(--green);font-size:10px">05</span> <span class="b">Lorem Ipsum</span> Lorem ipsum dolor sit amet.</div>
  <div class="abs p" style="left:170px;top:136px;width:130px"><span style="color:var(--green);font-size:10px">06</span> <span class="b">Lorem Ipsum</span> Lorem ipsum dolor sit amet.</div>
  <div class="foot">Your presentation title goes here</div><div class="num">5</div>
</section>

<!-- Row 4 -->
<section class="slide on-photo" style="left:95px;top:1407px">
  <div class="photo" style="inset:0;background:linear-gradient(135deg,#9fb88a,#d8cdb4 45%,#6d8a5a)" role="img" aria-label="Elderly couple smiling with their golden retriever outdoors"></div>
  <div class="abs" style="left:12px;right:12px;bottom:10px;height:28px;border-radius:14px;background:rgba(8,63,60,.85);display:flex;align-items:center;justify-content:space-between;padding:0 18px;color:#fff">
    <span style="display:flex;align-items:center;gap:3px;font-weight:700;font-size:10px"><i style="width:7px;height:7px;border-radius:50%;background:var(--green)"></i>Kernvital</span>
    <span style="font-size:12px;font-weight:500">SECTION <b style="color:var(--green)">BREAK</b></span>
  </div>
</section>

<section class="slide" style="left:453px;top:1407px">
  <div class="abs dark" style="left:0;top:0;width:210px;height:193px"></div>
  <div class="brand"><i></i>Kernvital</div>
  <div class="title" style="color:#fff;top:28px">Lorem <span class="hl">ipsum</span><br>dolor sit amet</div>
  <div class="abs p" style="left:32px;top:95px;width:120px;color:#d5e6e4">Lorem ipsum dolor sit amet, consectetuer adipiscing elit, sed diam nonummy nibh euismod tincidunt ut laoreet dolore magna aliquam erat volutpat. Ut wisi enim ad minim veniam, quis nostrud exerci tation ullamcorper suscipit lobortis nisl ut aliquip ex ea commodo consequat.</div>
  <div class="photo room frame" style="left:165px;top:58px;width:165px;height:100px" role="img" aria-label="Doctor showing a clipboard to an elderly woman"></div>
  <div class="num">4</div>
</section>

<section class="slide" style="left:811px;top:1407px">
  <div class="brand"><i></i>Kernvital</div>
  <div class="title" style="left:22px;top:25px">Slide <span class="hl">with</span><br>two images</div>
  <div class="photo room frame" style="left:118px;top:48px;width:80px;height:65px" role="img" aria-label="Elderly man exercising at home"></div>
  <div class="photo room frame" style="left:220px;top:48px;width:80px;height:65px" role="img" aria-label="Elderly woman stretching on a mat"></div>
  <div class="abs p" style="left:118px;top:125px;width:85px">Lorem ipsum dolor sit amet, consectetuer adipiscing elit, sed diam nonummy nibh euismod tincidunt ut laoreet dolore magna.</div>
  <div class="abs p" style="left:220px;top:125px;width:85px">Lorem ipsum dolor sit amet, consectetuer adipiscing elit, sed diam nonummy nibh euismod tincidunt ut laoreet dolore magna.</div>
  <div class="foot">Your presentation title goes here</div><div class="num">4</div>
</section>

<!-- Row 5 -->
<section class="slide" style="left:95px;top:1615px">
  <div class="brand"><i></i>Kernvital</div>
  <div class="title" style="left:37px;top:33px">Text <span class="hl">only</span> slide</div>
  <div class="abs p" style="left:37px;top:55px;width:270px;color:var(--teal);font-weight:600">Lorem ipsum dolor sit amet, consectetuer adipiscing elit, sed diam nonummy nibh euismod tincidunt ut laoreet dolore magna aliquam erat volutpat. Ut wisi enim ad minim veniam.</div>
  <div class="abs p" style="left:37px;top:75px;width:270px">Lorem ipsum dolor sit amet, consectetuer adipiscing elit, sed diam nonummy nibh euismod tincidunt ut laoreet dolore magna aliquam erat volutpat. Duis autem vel eum iriure dolor in hendrerit in vulputate velit esse molestie consequat, vel illum dolore eu feugiat nulla facilisis at vero eros et accumsan et iusto odio dignissim.</div>
  <div class="card" style="left:48px;top:118px;width:120px;height:42px"></div><div class="card" style="left:180px;top:118px;width:120px;height:42px"></div>
  <div class="abs p" style="left:55px;top:125px;width:105px"><span class="b">Lorem ipsum dolor sit amet</span><br>Lorem ipsum dolor sit amet, consectetuer adipiscing elit, sed diam nonummy nibh.</div>
  <div class="abs p" style="left:187px;top:125px;width:105px"><span class="b">Lorem ipsum dolor sit amet</span><br>Lorem ipsum dolor sit amet, consectetuer adipiscing elit, sed diam nonummy nibh.</div>
  <div class="foot">Your presentation title goes here</div><div class="num">6</div>
</section>

<section class="slide" style="left:453px;top:1615px">
  <div class="brand"><i></i>Kernvital</div>
  <div class="title" style="left:28px;top:16px">Our <span class="hl">Service</span> by year</div>
  <div class="abs p" style="left:30px;top:46px;width:150px">Lorem ipsum dolor sit amet, consectetuer adipiscing elit, sed diam nonummy nibh euismod tincidunt ut laoreet dolore magna.</div>
  <div class="card" style="left:200px;top:38px;width:52px;height:30px;text-align:center;font-size:11px;font-weight:700;padding-top:4px">30%<div style="font-size:4px;font-weight:500">Increases</div></div>
  <div class="card" style="left:260px;top:38px;width:52px;height:30px;text-align:center;font-size:11px;font-weight:700;padding-top:4px;color:var(--green)">20%<div style="font-size:4px;font-weight:500;color:var(--ink)">Decreases</div></div>
  <svg class="abs" style="left:22px;top:85px" width="300" height="95" viewBox="0 0 300 95">
    <defs><linearGradient id="gbar" x1="0" y1="0" x2="0" y2="1"><stop offset="0" stop-color="#8cc63f"/><stop offset="1" stop-color="#0b5550"/></linearGradient></defs>
    <g stroke="#eceeee" stroke-width=".5"><line x1="12" y1="5" x2="295" y2="5"/><line x1="12" y1="23" x2="295" y2="23"/><line x1="12" y1="41" x2="295" y2="41"/><line x1="12" y1="59" x2="295" y2="59"/><line x1="12" y1="77" x2="295" y2="77"/></g>
    <g fill="url(#gbar)">
      <rect x="18" y="60" width="6" height="17"/><rect x="26" y="66" width="6" height="11"/>
      <rect x="42" y="56" width="6" height="21"/><rect x="50" y="62" width="6" height="15"/>
      <rect x="66" y="52" width="6" height="25"/><rect x="74" y="60" width="6" height="17"/>
      <rect x="90" y="48" width="6" height="29"/><rect x="98" y="58" width="6" height="19"/>
      <rect x="114" y="40" width="6" height="37"/><rect x="122" y="52" width="6" height="25"/>
      <rect x="138" y="46" width="6" height="31"/><rect x="146" y="56" width="6" height="21"/>
      <rect x="162" y="54" width="6" height="23"/><rect x="170" y="62" width="6" height="15"/>
      <rect x="186" y="44" width="6" height="33"/><rect x="194" y="54" width="6" height="23"/>
      <rect x="210" y="34" width="6" height="43"/><rect x="218" y="46" width="6" height="31"/>
      <rect x="234" y="30" width="6" height="47"/><rect x="242" y="40" width="6" height="37"/>
      <rect x="258" y="26" width="6" height="51"/><rect x="266" y="36" width="6" height="41"/>
      <rect x="282" y="32" width="6" height="45"/>
    </g>
    <polyline fill="none" stroke="#9aa7a5" stroke-width=".7" points="22,58 46,52 70,46 94,40 118,32 142,40 166,50 190,30 214,18 238,26 262,16 286,28"/>
    <rect x="104" y="22" width="34" height="7" rx="1.5" fill="#8cc63f"/><text x="121" y="27" font-size="3.5" fill="#fff" text-anchor="middle" font-family="Montserrat,sans-serif">Best Perform</text>
    <g font-size="3.5" fill="#8a9897" font-family="Montserrat,sans-serif" text-anchor="middle"><text x="25" y="86">January</text><text x="49" y="86">February</text><text x="73" y="86">March</text><text x="97" y="86">April</text><text x="121" y="86">May</text><text x="145" y="86">June</text><text x="169" y="86">July</text><text x="193" y="86">August</text><text x="217" y="86">September</text><text x="241" y="86">October</text><text x="265" y="86">November</text><text x="287" y="86">December</text></g>
  </svg>
  <div class="foot">Your presentation title goes here</div><div class="num">7</div>
</section>

<section class="slide" style="left:811px;top:1615px">
  <div class="brand"><i></i>Kernvital</div>
  <div class="title" style="left:28px;top:16px">Lorem <span class="hl">Ipsum</span> Slide</div>
  <div class="card frame" style="left:28px;top:40px;width:170px;height:132px;border-top:3px solid var(--green);border-radius:0 8px 8px 0"></div>
  <svg class="abs" style="left:35px;top:50px" width="155" height="115" viewBox="0 0 155 115">
    <g stroke="#eceeee" stroke-width=".5"><line x1="8" y1="10" x2="150" y2="10"/><line x1="8" y1="30" x2="150" y2="30"/><line x1="8" y1="50" x2="150" y2="50"/><line x1="8" y1="70" x2="150" y2="70"/><line x1="8" y1="90" x2="150" y2="90"/></g>
    <g><rect x="20" y="82" width="5" height="8" fill="#0b5550"/><rect x="26" y="78" width="5" height="12" fill="#8cc63f"/><rect x="32" y="72" width="5" height="18" fill="#d0d5d4"/>
    <rect x="44" y="70" width="5" height="20" fill="#0b5550"/><rect x="50" y="62" width="5" height="28" fill="#8cc63f"/><rect x="56" y="74" width="5" height="16" fill="#d0d5d4"/>
    <rect x="68" y="62" width="5" height="28" fill="#0b5550"/><rect x="74" y="52" width="5" height="38" fill="#8cc63f"/><rect x="80" y="66" width="5" height="24" fill="#d0d5d4"/>
    <rect x="92" y="52" width="5" height="38" fill="#0b5550"/><rect x="98" y="40" width="5" height="50" fill="#8cc63f"/><rect x="104" y="56" width="5" height="34" fill="#d0d5d4"/>
    <rect x="116" y="40" width="5" height="50" fill="#0b5550"/><rect x="122" y="22" width="5" height="68" fill="#8cc63f"/><rect x="128" y="30" width="5" height="60" fill="#d0d5d4"/></g>
    <g font-size="3" fill="#8a9897" font-family="Montserrat,sans-serif"><text x="8" y="100">■ Series 1</text><text x="8" y="105">■ Series 2</text><text x="8" y="110">■ Series 3</text><text x="22" y="95">Category 1</text><text x="46" y="95">Category 2</text><text x="70" y="95">Category 3</text><text x="94" y="95">Category 4</text><text x="118" y="95">Category 5</text></g>
  </svg>
  <div class="abs p" style="left:215px;top:48px;width:100px">Lorem ipsum dolor sit amet, consectetuer adipiscing elit, sed diam nonummy nibh euismod tincidunt ut laoreet dolore.</div>
  <div class="tick" style="left:215px;top:78px;background:none;border:1px solid var(--green)"></div><div class="abs p" style="left:230px;top:76px;width:85px"><span class="g">Value One</span><br>Lorem ipsum dolor sit amet, sed diam nonummy nibh.</div>
  <div class="tick" style="left:215px;top:106px;background:none;border:1px solid var(--green)"></div><div class="abs p" style="left:230px;top:104px;width:85px"><span class="g">Value Two</span><br>Lorem ipsum dolor sit amet, sed diam nonummy nibh.</div>
  <div class="tick" style="left:215px;top:134px;background:none;border:1px solid var(--green)"></div><div class="abs p" style="left:230px;top:132px;width:85px"><span class="g">Value Three</span><br>Lorem ipsum dolor sit amet, sed diam nonummy nibh.</div>
  <div class="foot">Your presentation title goes here</div><div class="num">5</div>
</section>

<!-- Row 6 -->
<section class="slide" style="left:95px;top:1824px">
  <div class="title" style="top:26px">Innovation to<br><span class="hl">Resolve</span> Problems</div>
  <div class="abs p" style="left:32px;top:64px;width:150px">Lorem ipsum dolor sit amet, consectetuer adipiscing elit, sed diam nonummy nibh euismod tincidunt ut laoreet dolore magna aliquam erat volutpat.</div>
  <div class="abs p" style="left:32px;top:98px;width:135px">
    <div style="display:flex;justify-content:space-between">Lorem ipsum dolor sit amet, consectetuer<span>80%</span></div><div class="bar-row"><i style="width:80%"></i></div>
    <div style="display:flex;justify-content:space-between">Lorem ipsum dolor sit amet, consectetuer<span>92%</span></div><div class="bar-row"><i style="width:92%"></i></div>
    <div style="display:flex;justify-content:space-between">Lorem ipsum dolor sit amet, consectetuer<span>68%</span></div><div class="bar-row"><i style="width:68%"></i></div>
  </div>
  <div class="photo grey" style="left:207px;top:5px;width:130px;height:183px;border-right:3px solid var(--green);border-bottom:3px solid var(--green);border-radius:0 0 8px 0" role="img" aria-label="Portrait of a smiling elderly man with glasses"></div>
  <div class="brand" style="color:#fff"><i></i>Kernvital</div>
  <div class="foot">Your presentation title goes here</div>
</section>

<section class="slide" style="left:453px;top:1824px">
  <div class="brand"><i></i>Kernvital</div>
  <div class="title" style="left:0;right:0;top:20px;text-align:center">The <span class="hl">Line</span> Chart</div>
  <div class="abs p" style="left:90px;top:40px;width:165px;text-align:center">Lorem ipsum dolor sit amet, consectetuer adipiscing elit, sed diam nonummy nibh euismod tincidunt ut laoreet dolore magna.</div>
  <div class="card" style="left:22px;top:62px;width:300px;height:110px;border-bottom:3px solid var(--green);border-left:3px solid var(--green);border-right:3px solid var(--green);border-radius:0 0 8px 8px"></div>
  <svg class="abs" style="left:30px;top:72px" width="285" height="95" viewBox="0 0 285 95">
    <g stroke="#eceeee" stroke-width=".5"><line x1="10" y1="10" x2="280" y2="10"/><line x1="10" y1="25" x2="280" y2="25"/><line x1="10" y1="40" x2="280" y2="40"/><line x1="10" y1="55" x2="280" y2="55"/><line x1="10" y1="70" x2="280" y2="70"/></g>
    <polyline fill="none" stroke="#0b5550" stroke-width=".8" points="40,48 110,30 180,40 250,20"/>
    <polyline fill="none" stroke="#8cc63f" stroke-width=".8" points="40,30 110,44 180,22 250,26"/>
    <polyline fill="none" stroke="#9aa7a5" stroke-width=".8" points="40,56 110,50 180,36 250,30"/>
    <g font-size="3.5" fill="#8a9897" font-family="Montserrat,sans-serif" text-anchor="middle"><text x="40" y="80">Category 1</text><text x="110" y="80">Category 2</text><text x="180" y="80">Category 3</text><text x="250" y="80">Category 4</text><text x="145" y="90">— Series 1   — Series 2   — Series 3</text></g>
  </svg>
  <div class="foot">Your presentation title goes here</div><div class="num">6</div>
</section>

<section class="slide" style="left:811px;top:1824px">
  <div class="brand"><i></i>Kernvital</div>
  <div class="title" style="left:38px;top:22px">Timeline <span class="hl">slide</span></div>
  <svg class="abs" style="left:0;top:0" width="343" height="193" viewBox="0 0 343 193">
    <line x1="50" y1="110" x2="265" y2="110" stroke="#0b5550" stroke-width="1"/>
    <g fill="#fff" stroke="#8cc63f" stroke-width="1.5"><circle cx="52" cy="110" r="9"/><circle cx="120" cy="110" r="9"/><circle cx="188" cy="110" r="9"/><circle cx="258" cy="110" r="9"/></g>
    <g fill="#8cc63f"><circle cx="52" cy="110" r="6"/><circle cx="120" cy="110" r="6"/><circle cx="188" cy="110" r="6"/><circle cx="258" cy="110" r="6"/></g>
    <g stroke="#c8d0cf" stroke-width=".5"><line x1="56" y1="120" x2="56" y2="150"/><line x1="124" y1="100" x2="124" y2="62"/><line x1="192" y1="120" x2="192" y2="150"/><line x1="262" y1="100" x2="262" y2="62"/></g>
  </svg>
  <div class="abs p" style="left:58px;top:132px;width:60px"><span class="b">TIMELINE 1</span><br>Lorem ipsum dolor sit amet, consectetuer adipiscing elit.</div>
  <div class="abs p" style="left:126px;top:60px;width:60px"><span class="b">TIMELINE 2</span><br>Lorem ipsum dolor sit amet, consectetuer adipiscing elit.</div>
  <div class="abs p" style="left:194px;top:132px;width:60px"><span class="b">TIMELINE 3</span><br>Lorem ipsum dolor sit amet, consectetuer adipiscing elit.</div>
  <div class="abs p" style="left:264px;top:60px;width:60px"><span class="b">TIMELINE 4</span><br>Lorem ipsum dolor sit amet, consectetuer adipiscing elit.</div>
  <div class="foot">Your presentation title goes here</div><div class="num">5</div>
</section>

<!-- Row 7 -->
<section class="slide" style="left:95px;top:2033px">
  <div class="brand"><i></i>Kernvital</div>
  <div class="title" style="left:38px;top:22px">Our <span class="hl">Monthly</span> Plan</div>
  <div class="abs p" style="left:40px;top:70px;width:85px">• Lorem ipsum dolor sit amet, consectetuer adipiscing elit.<br>• Lorem ipsum dolor sit amet<br>• Lorem ipsum dolor sit amet, consectetuer adipiscing elit.</div>
  <div class="abs p" style="left:140px;top:70px;width:85px">• Lorem ipsum dolor sit amet, consectetuer adipiscing elit.<br>• Lorem ipsum dolor sit amet<br>• Lorem ipsum dolor sit amet, consectetuer adipiscing elit.</div>
  <div class="abs p" style="left:240px;top:70px;width:85px">• Lorem ipsum dolor sit amet, consectetuer adipiscing elit.<br>• Lorem ipsum dolor sit amet<br>• Lorem ipsum dolor sit amet, consectetuer adipiscing elit.</div>
  <svg class="abs" style="left:0;top:125px" width="343" height="20" viewBox="0 0 343 20">
    <defs><linearGradient id="garr" x1="0" x2="1"><stop offset="0" stop-color="#8cc63f" stop-opacity="0"/><stop offset="1" stop-color="#8cc63f"/></linearGradient></defs>
    <g fill="url(#garr)"><path d="M30 9h75v-3l7 4-7 4v-3H30z"/><path d="M130 9h75v-3l7 4-7 4v-3h-75z"/><path d="M230 9h75v-3l7 4-7 4v-3h-75z"/></g>
  </svg>
  <div class="abs" style="left:40px;top:150px;width:275px;display:flex;justify-content:space-around;color:var(--green);font-size:11px">
    <span>January</span><span>February</span><span>March</span></div>
  <div class="foot">Your presentation title goes here</div><div class="num">5</div>
</section>

<section class="slide" style="left:453px;top:2033px">
  <div class="brand"><i></i>Kernvital</div>
  <div class="title" style="top:22px">Custom Editable<br><span class="hl">Pie Chart</span> Slide</div>
  <div class="abs p" style="left:32px;top:68px;width:120px"><span style="color:var(--green);font-size:10px;float:left;margin-right:6px">60 %</span><span class="b">CHART 1 DETAILS</span><br>Lorem ipsum dolor sit amet, consectetuer adipiscing elit.</div>
  <div class="abs p" style="left:32px;top:102px;width:120px"><span style="color:var(--green);font-size:10px;float:left;margin-right:6px">60 %</span><span class="b">CHART 2 DETAILS</span><br>Lorem ipsum dolor sit amet, consectetuer adipiscing elit.</div>
  <div class="abs p" style="left:32px;top:136px;width:120px"><span style="color:var(--green);font-size:10px;float:left;margin-right:6px">60 %</span><span class="b">CHART 3 DETAILS</span><br>Lorem ipsum dolor sit amet, consectetuer adipiscing elit.</div>
  <svg class="abs" style="left:190px;top:40px" width="140" height="140" viewBox="0 0 140 140">
    <circle cx="70" cy="70" r="55" fill="none" stroke="#0b5550" stroke-width="14" stroke-dasharray="260 400" transform="rotate(-90 70 70)"/>
    <circle cx="70" cy="70" r="40" fill="none" stroke="#8cc63f" stroke-width="12" stroke-dasharray="200 400" transform="rotate(-40 70 70)"/>
    <circle cx="70" cy="70" r="28" fill="none" stroke="#2f7d62" stroke-width="8" stroke-dasharray="120 400" transform="rotate(60 70 70)"/>
    <text x="70" y="66" font-size="8" text-anchor="middle" fill="#1d3a3a" font-family="Montserrat,sans-serif">Year</text>
    <text x="70" y="78" font-size="11" font-weight="700" text-anchor="middle" fill="#1d3a3a" font-family="Montserrat,sans-serif">2025</text>
    <rect x="2" y="24" width="16" height="7" fill="#0b5550"/><text x="10" y="29" font-size="3.5" fill="#fff" text-anchor="middle" font-family="Montserrat,sans-serif">60%</text>
    <rect x="86" y="26" width="16" height="7" fill="#8cc63f"/><text x="94" y="31" font-size="3.5" fill="#fff" text-anchor="middle" font-family="Montserrat,sans-serif">60%</text>
    <rect x="100" y="70" width="16" height="7" fill="#2f7d62"/><text x="108" y="75" font-size="3.5" fill="#fff" text-anchor="middle" font-family="Montserrat,sans-serif">60%</text>
  </svg>
  <div class="foot">Your presentation title goes here</div><div class="num">4</div>
</section>

<section class="slide" style="left:811px;top:2033px">
  <div class="brand"><i></i>Kernvital</div>
  <div class="title" style="top:22px">Custom Editable<br><span class="hl">Pie Chart</span> Slide</div>
  <svg class="abs" style="left:0;top:70px" width="343" height="45" viewBox="0 0 343 45">
    <g fill="none" stroke-width="3" stroke-linecap="round">
      <circle cx="85" cy="24" r="16" stroke="#8cc63f" stroke-dasharray="88 200" transform="rotate(180 85 24)"/>
      <circle cx="145" cy="24" r="16" stroke="#0b5550" stroke-dasharray="70 200" transform="rotate(180 145 24)"/>
      <circle cx="205" cy="24" r="16" stroke="#9aa7a5" stroke-dasharray="30 200" transform="rotate(180 205 24)"/>
      <circle cx="265" cy="24" r="16" stroke="#3fa6b0" stroke-dasharray="70 200" transform="rotate(180 265 24)"/>
    </g>
    <g font-size="11" text-anchor="middle" font-family="Montserrat,sans-serif"><text x="85" y="32" fill="#8cc63f">88%</text><text x="145" y="32" fill="#0b5550">70%</text><text x="205" y="32" fill="#6b7b7a">30%</text><text x="265" y="32" fill="#3fa6b0">70%</text></g>
  </svg>
  <div class="abs p" style="left:62px;top:120px;width:46px;text-align:center"><span class="g" style="color:#e0703a">CHART 1 DETAILS</span><br>Lorem ipsum dolor sit amet, consectetuer adipiscing elit.</div>
  <div class="abs p" style="left:122px;top:120px;width:46px;text-align:center"><span class="b">CHART 2 DETAILS</span><br>Lorem ipsum dolor sit amet, consectetuer adipiscing elit.</div>
  <div class="abs p" style="left:182px;top:120px;width:46px;text-align:center"><span class="b">CHART 3 DETAILS</span><br>Lorem ipsum dolor sit amet, consectetuer adipiscing elit.</div>
  <div class="abs p" style="left:242px;top:120px;width:46px;text-align:center"><span class="b">CHART 4 DETAILS</span><br>Lorem ipsum dolor sit amet, consectetuer adipiscing elit.</div>
  <div class="foot">Your presentation title goes here</div><div class="num">5</div>
</section>

<!-- Row 8 -->
<section class="slide" style="left:95px;top:2242px">
  <div class="abs dark" style="left:210px;top:0;width:133px;height:193px"></div>
  <div class="brand" style="color:#fff"><i></i>Kernvital</div>
  <div class="title" style="left:38px;top:20px">Comparrison <span class="hl">Table</span></div>
  <div class="card" style="left:28px;top:40px;width:292px;height:130px;padding:8px 10px">
    <table>
      <tr><th></th><th style="background:var(--teal);color:#fff;text-align:center">COMPETITORS</th><th style="background:var(--green);color:#fff;text-align:center">KERNVITAL</th></tr>
      <tr><td class="p"><span class="g" style="color:var(--teal)">Lorem ipsum</span><br>Lorem ipsum dolor sit amet, consectetuer adipiscing elit.</td><td class="p">Lorem ipsum dolor sit amet, consectetuer adipiscing.</td><td class="p">Lorem ipsum dolor sit amet, consectetuer adipiscing.</td></tr>
      <tr><td class="p"><span class="g" style="color:var(--teal)">Lorem ipsum</span><br>Lorem ipsum dolor sit amet, consectetuer adipiscing elit.</td><td class="p">Lorem ipsum dolor sit amet, consectetuer adipiscing.</td><td class="p">Lorem ipsum dolor sit amet, consectetuer adipiscing.</td></tr>
      <tr><td class="p"><span class="g" style="color:var(--teal)">Lorem ipsum</span><br>Lorem ipsum dolor sit amet, consectetuer adipiscing elit.</td><td class="p">Lorem ipsum dolor sit amet, consectetuer adipiscing.</td><td class="p">Lorem ipsum dolor sit amet, consectetuer adipiscing.</td></tr>
    </table>
  </div>
  <div class="foot">Your presentation title goes here</div>
</section>

<section class="slide" style="left:453px;top:2242px">
  <div class="brand"><i></i>Kernvital</div>
  <div class="title" style="left:36px;top:22px">The <span class="hl">Table</span> Slide</div>
  <div class="abs p" style="left:36px;top:44px;width:150px">Lorem ipsum dolor sit amet, consectetuer adipiscing elit, sed diam nonummy nibh euismod tincidunt ut laoreet dolore.</div>
  <div class="abs" style="left:215px;top:42px;border:1px solid var(--green);border-radius:3px;padding:1px 5px;font-size:4px;color:var(--green);text-align:center;font-weight:600">Research By<br><span style="color:var(--muted);font-weight:400">University Study</span></div>
  <div class="abs" style="left:36px;top:68px;width:275px">
    <table>
      <tr style="background:var(--green);color:#fff"><th style="background:var(--teal)">Label Here</th><th>Title</th><th>Title</th><th>Title</th><th>Title</th><th>Title</th></tr>
      <tr style="border-bottom:1px solid var(--line)"><td class="b" style="font-size:3.5px">Lorem Ipsum Dolor Sit</td><td>10653 Million</td><td>7890 Million</td><td>456 Million</td><td>3567 Million</td><td>7890 Million</td></tr>
      <tr style="border-bottom:1px solid var(--line)"><td class="b" style="font-size:3.5px">Lorem Ipsum Dolor Sit</td><td>456 Million</td><td>104 Million</td><td>7890 Million</td><td>10653 Million</td><td>3567 Million</td></tr>
      <tr style="border-bottom:1px solid var(--line)"><td class="b" style="font-size:3.5px">Lorem Ipsum Dolor Sit</td><td>104 Million</td><td>104 Million</td><td>7890 Million</td><td>104 Million</td><td>104 Million</td></tr>
      <tr style="border-bottom:1px solid var(--line)"><td class="b" style="font-size:3.5px">Lorem Ipsum Dolor Sit</td><td>7890 Million</td><td>3567 Million</td><td>10653 Million</td><td>3567 Million</td><td>3567 Million</td></tr>
      <tr style="border-bottom:1px solid var(--line)"><td class="b" style="font-size:3.5px">Lorem Ipsum Dolor Sit</td><td>3567 Million</td><td>104 Million</td><td>456 Million</td><td>10653 Million</td><td>104 Million</td></tr>
      <tr style="border-bottom:1px solid var(--line)"><td class="b" style="font-size:3.5px">Lorem Ipsum Dolor Sit</td><td>10653 Million</td><td>3567 Million</td><td>3567 Million</td><td>456 Million</td><td>10653 Million</td></tr>
    </table>
    <div class="p" style="text-align:right;margin-top:4px"><span class="g">Note:</span> Lorem ipsum dolor sit amet, consectetuer adipiscing elit, sed diam volutpat.</div>
  </div>
  <div class="foot">Your presentation title goes here</div><div class="num">5</div>
</section>

<section class="slide dark" style="left:811px;top:2242px">
  <div class="abs" style="left:0;right:0;top:55px;display:flex;justify-content:center;align-items:center;gap:3px;font-weight:700;font-size:10px"><i style="width:7px;height:7px;border-radius:50%;background:var(--green)"></i>Kernvital</div>
  <div class="abs" style="left:0;right:0;top:78px;text-align:center;font-size:18px;font-weight:500">VIELEN <b style="color:var(--green)">DANK.</b></div>
  <div class="abs p" style="left:110px;top:113px;width:70px"><span class="g">Kernvital GmbH</span><br>Lindenweg 14<br>60311 Frankfurt</div>
  <div class="abs p" style="left:185px;top:113px;width:80px">Telephone: 069 1234 560<br>E-Mail: info@kernvital.de<br>Web: www.kernvital.de</div>
</section>

</body>
</html>
```